Property Developer - Simple yet Sophisticated and Sharp Business Card

We are a medium sized property developer involved mainly in townhouse developments and land subdivisions.

The company is looking for a simple, sharp and sophisticated business card that will be given to contractors, land owners, financiers etc and thus will need to look professional.

Property development related graphics and art can be used, however the card is not to be too "busy" or crowded. Our company name is Kestrel Developments which could possibly be incorporated into the graphics or artwork.

Single sided and/or double sided designs will be acceptable.

A Simple, Sophisticated, Sharp design please!

Good Luck !

```html
<!DOCTYPE html>
<html lang="en">
<head>
<meta charset="utf-8">
<title>Kestrel Developments – Business Card</title>
<link rel="stylesheet" href="https://fonts.googleapis.com/css2?family=Arimo:wght@400;700&display=swap">
<style>
  :root {
    --backdrop: #e4e4e4;
    --card: #ffffff;
    --leaf: #8cc43f;
    --leaf-edge: #5f9e22;
    --ink: #111111;
    --slate: #6d6e71;
    --paper-text: #ffffff;
  }
  * { box-sizing: border-box; margin: 0; padding: 0; }
  html, body { width: 1200px; height: 900px; overflow: hidden; }
  body {
    background: var(--backdrop);
    font-family: "Arimo", Arial, sans-serif;
    position: relative;
  }
  .card {
    position: absolute;
    left: 255px;
    width: 660px;
    height: 362px;
    background: var(--card);
    overflow: hidden;
  }
  .card--front { top: 52px; }
  .card--back { top: 446px; }

  .front-sweep { position: absolute; inset: 0; width: 100%; height: 100%; }

  .brand-name {
    position: absolute;
    color: var(--slate);
    font-weight: 700;
    text-transform: uppercase;
    letter-spacing: 0.5px;
    display: flex;
    align-items: center;
  }
  .brand-mark {
    display: inline-block;
    background: var(--leaf);
  }
  .card--front .brand-name {
    left: 28px;
    top: 58px;
    font-size: 17px;
    gap: 10px;
    width: 200px;
    line-height: 1.15;
  }
  .card--front .brand-mark { width: 22px; height: 22px; flex: none; }

  .holder {
    position: absolute;
    right: 37px;
    top: 30px;
    text-align: right;
  }
  .holder-name {
    color: var(--paper-text);
    font-weight: 700;
    font-size: 30px;
    line-height: 1;
  }
  .holder-role {
    color: var(--slate);
    font-size: 15px;
    line-height: 1;
    margin-top: 4px;
    text-transform: uppercase;
  }

  .contact {
    position: absolute;
    left: 50px;
    top: 229px;
    display: grid;
    grid-template-columns: 132px auto;
    row-gap: 6px;
    font-size: 16px;
    line-height: 20px;
  }
  .contact-label {
    color: var(--paper-text);
    font-weight: 700;
    text-align: right;
  }
  .contact-value { color: var(--ink); letter-spacing: 0.3px; }

  .card--back .brand-name {
    left: 0;
    right: 0;
    top: 150px;
    justify-content: center;
    font-size: 34px;
    gap: 16px;
  }
  .card--back .brand-mark { width: 36px; height: 36px; }
</style>
</head>
<body>
  <section class="card card--front" aria-label="Business card, front">
    <svg class="front-sweep" viewBox="0 0 660 362" preserveAspectRatio="none" aria-hidden="true">
      <path d="M438,0 C250,40 70,180 0,362 L660,362 L660,0 Z" fill="var(--leaf)"/>
      <path d="M438,0 C250,40 70,180 0,362" fill="none" stroke="var(--leaf-edge)" stroke-width="5"/>
    </svg>

    <div class="brand-name"><span class="brand-mark"></span><span>Kestrel Developments</span></div>

    <div class="holder">
      <p class="holder-name">YOUR NAME</p>
      <p class="holder-role">Marketing</p>
    </div>

    <dl class="contact">
      <dt class="contact-label">Phone:</dt><dd class="contact-value">(07) 5550 1824</dd>
      <dt class="contact-label">Fax:</dt><dd class="contact-value">(07) 5550 1825</dd>
      <dt class="contact-label">Postal:</dt><dd class="contact-value">PO Box 2874 Brookfield Vale QLD 4075</dd>
      <dt class="contact-label">Email:</dt><dd class="contact-value">projects@kestrel-developments.example</dd>
    </dl>
  </section>

  <section class="card card--back" aria-label="Business card, back">
    <div class="brand-name"><span class="brand-mark"></span><span>Kestrel Developments</span></div>
  </section>
</body>
</html>
```